Business Card Design needed for start up company Halvora

In need of a new business card designed for a start up company based in Sydney, Halvora is a new start up innovative Company, our mission it to make property accessible for everyday Australian and to become the leading Real Estate platform in Australia. We want it to be fresh and clean.

Industry/Entity Type

Financial

Contact Information for Business Card

Section for Name
Section for Title

HALVORA - The Strength of Pooling
Mobile:
Direct:

Font styles to use
Sans Serif

Colors
33a6d7
0692cd
0255a3
ffffff

Requirements
Must have
• Logo, all business card details

```html
<!DOCTYPE html>
<html lang="en">
<head>
<meta charset="utf-8">
<title>Halvora Business Card</title>
<link rel="stylesheet" href="https://fonts.googleapis.com/css2?family=Open+Sans:wght@400;600;700;800&display=swap">
<style>
  :root {
    --sky: #33a6d7;
    --cyan: #2fd0e6;
    --ocean: #0692cd;
    --navy: #0255a3;
    --ink: #1d3a78;
    --deep: #13285f;
    --white: #ffffff;
    --paper: #f4f5f6;
    --text: #3c3c3c;
    --stage: #e4e6e9;
  }
  * { box-sizing: border-box; margin: 0; padding: 0; }
  html, body {
    width: 1200px; height: 900px; overflow: hidden;
    background: var(--stage);
    font-family: "Open Sans", Arial, sans-serif;
  }
  .stage { position: relative; width: 1200px; height: 900px; }
  .card {
    position: absolute;
    width: 560px; height: 320px;
    border-radius: 4px;
    box-shadow: 0 8px 24px rgba(0,0,0,0.18);
    overflow: hidden;
  }
  /* Front */
  .card--front {
    left: 320px; top: 105px;
    background: linear-gradient(110deg, var(--cyan) 0%, var(--sky) 45%, var(--ocean) 100%);
    color: var(--white);
  }
  .front-logo {
    position: absolute; left: 50%; top: 118px;
    transform: translateX(-50%);
    display: flex; align-items: center; gap: 12px;
    white-space: nowrap;
  }
  .logo-dot {
    flex: none;
    width: 54px; height: 54px; border-radius: 50%;
    background: var(--white);
  }
  .logo-name {
    font-weight: 800; font-size: 52px; letter-spacing: 1px; line-height: 1;
    white-space: nowrap;
  }
  .front-tagline {
    position: absolute; left: 0; right: 0; top: 210px;
    text-align: center; font-size: 14px; font-weight: 400;
  }
  /* Back */
  .card--back {
    left: 320px; top: 475px;
    background: var(--paper);
    color: var(--text);
  }
  .contact-list {
    position: absolute; left: 34px; top: 40px;
    font-size: 14px; line-height: 21px; list-style: none;
  }
  .contact-list b { color: var(--ink); font-weight: 700; margin-right: 4px; }
  .name-band {
    position: absolute; left: 0; top: 128px;
    width: 300px; height: 62px;
    background: linear-gradient(90deg, var(--deep) 0%, var(--navy) 100%);
    color: var(--white);
    padding: 10px 0 0 34px;
  }
  .person-name { font-weight: 700; font-size: 17px; line-height: 22px; }
  .person-title { font-weight: 400; font-size: 14px; line-height: 20px; }
  .back-logo {
    position: absolute; left: 278px; top: 121px;
    display: flex; align-items: center; gap: 8px;
  }
  .back-logo .logo-dot {
    width: 76px; height: 76px;
    background: var(--ocean);
    border: 4px solid var(--white);
  }
  .back-logo .logo-name {
    color: var(--ink); font-size: 30px; letter-spacing: 0.5px;
  }
  .address {
    position: absolute; left: 34px; bottom: 30px;
    font-size: 14px; line-height: 20px; font-style: normal;
  }
  .address .web { color: var(--ink); font-weight: 700; letter-spacing: 1px; }
</style>
</head>
<body>
<main class="stage">
  <section class="card card--front" aria-label="Card front">
    <div class="front-logo">
      <span class="logo-dot"></span>
      <span class="logo-name">HALVORA</span>
    </div>
    <p class="front-tagline">The Strength of Pooling</p>
  </section>

  <section class="card card--back" aria-label="Card back">
    <ul class="contact-list">
      <li><b>Phone:</b> 612 480 3917</li>
      <li><b>Mob:</b> 614 225 7086</li>
      <li><b>Email:</b> hello@halvora.au</li>
    </ul>
    <div class="name-band">
      <p class="person-name">MARCUS HALE</p>
      <p class="person-title">CEO/FOUNDER</p>
    </div>
    <div class="back-logo">
      <span class="logo-dot"></span>
      <span class="logo-name">HALVORA</span>
    </div>
    <address class="address">
      42 Wattle Grove<br>
      Sydney, NSW 2000<br>
      <span class="web">www.halvora.au</span>
    </address>
  </section>
</main>
</body>
</html>
```